High value cover design for an A4 ideation pad.

The product is NOT A BOOK.

It's an A4 ideation pad for professionals, designers and creators who handwrite their ideas. Visualise creators like Milo Varnet, Owen Plaskit and Gregor Lunwick in your mind's eye.

I'm looking for a cover design for the ideation pad. Both front and back.

It should look, feel and convey the following.

--> A handcrafted product experience

--> High value & Elegance

--> Inspiration

Mandatory --> See Uploaded Files --> Files 1, 5 & 6

Target Market(s)

- Designers

-Creative Professionals

- Entrepreneurs

who handwrite their ideas. Visualise creators like Milo Varnet, Owen Plaskit and Gregor Lunwick in your mind's eye.

Industry/Entity Type

Stationary

Font styles to use
Script
Other font styles liked:
• Calligraphy

Colors
fbed22

Requirements
Must have
• Title text - Quiet Kettle Notes

-Text in gold on brown leather background to convey high value for the front cover.

--> High value & Elegance

--> Inspiration

--> Should compel the customers to pick up and own the idea pad
Nice to have
• That's my take but other ideas are welcome
Should not have
• Must not convey

- low value

```html
<!DOCTYPE html>
<html lang="en">
<head>
<meta charset="utf-8">
<title>Quiet Kettle Notes — Ideation Pad Cover</title>
<link rel="stylesheet" href="https://fonts.googleapis.com/css2?family=Great+Vibes&display=swap">
<style>
  :root {
    --paper: #ffffff;
    --cover-black: #000000;
    --gold-light: #f2d36b;
    --gold-mid: #d4a52a;
    --gold-deep: #a8780e;
    --gold-glow: rgba(180, 130, 30, 0.35);
  }
  html, body {
    margin: 0;
    padding: 0;
    width: 1200px;
    height: 832px;
    overflow: hidden;
    background: var(--paper);
  }
  .spread {
    position: relative;
    width: 1200px;
    height: 832px;
  }
  .cover {
    position: absolute;
    background: var(--cover-black);
    overflow: hidden;
  }
  .cover--front {
    left: 36px;
    top: 24px;
    width: 556px;
    height: 786px;
  }
  .cover--back {
    left: 617px;
    top: 22px;
    width: 556px;
    height: 785px;
  }
  .pad-title {
    position: absolute;
    left: 0;
    width: 100%;
    top: 300px;
    margin: 0;
    text-align: center;
    font-family: "Great Vibes", cursive;
    font-weight: 400;
    font-size: 60px;
    line-height: 60px;
    background: linear-gradient(180deg, var(--gold-light) 0%, var(--gold-mid) 45%, var(--gold-deep) 100%);
    -webkit-background-clip: text;
    background-clip: text;
    color: transparent;
  }
  .pad-title span { display: block; }
  .back-pattern {
    position: absolute;
    inset: 0;
    background:
      linear-gradient(135deg, var(--cover-black) 0%, var(--gold-glow) 50%, var(--cover-black) 100%);
  }
</style>
</head>
<body>
<main class="spread">
  <section class="cover cover--front" aria-label="Front cover">
    <h1 class="pad-title"><span>Quiet</span><span>Kettle</span><span>Notes</span></h1>
  </section>

  <section class="cover cover--back" aria-label="Back cover">
    <div class="back-pattern" role="img" aria-label="Decorative pattern of flowing gold lines on black"></div>
  </section>
</main>
</body>
</html>
```